Specialised investor in e-mobility and energy wants business card design

We need a business card design that fits our existing corporate design. <The look and feel must be 'sharp'/'clean', dynamic, communicate momentum, professionalism etc (as one would imagine from a firm in the financial sector). We like the idea of a reverse-side of the card that includes the logo, and the name and contact details on the other. We expect the deliverable to be whatever format might be required to be able to get cards printed directly by a service such as kelmo press. Our website is www.zub.capital

```html
<!DOCTYPE html>
<html lang="en">
<head>
<meta charset="utf-8">
<title>Zub Capital – Business Card</title>
<link href="https://fonts.googleapis.com/css2?family=Montserrat:wght@400;500;800&display=swap" rel="stylesheet">
<style>
  :root {
    --backdrop: #2c2f34;
    --forest: #324f24;
    --lime: #84bc3a;
    --paper: #ffffff;
    --ink: #2b4a1c;
    --muted: #6f7570;
    --text: #3a3f3b;
  }
  * { box-sizing: border-box; margin: 0; padding: 0; }
  html, body {
    width: 1200px; height: 952px; overflow: hidden;
    background: var(--backdrop);
    font-family: "Montserrat", Arial, sans-serif;
  }
  .sheet {
    position: relative; width: 1200px; height: 952px;
    display: flex; align-items: center; justify-content: center; gap: 40px;
  }
  .card {
    position: relative; width: 525px; height: 300px;
    border-radius: 22px; overflow: hidden;
    box-shadow: 0 18px 40px rgba(0,0,0,.35);
  }

  /* Front: contact side */
  .card--front { background: var(--paper); }
  .holder { position: absolute; left: 38px; top: 34px; }
  .holder__name {
    font-weight: 800; font-size: 21px; letter-spacing: .5px;
    color: var(--ink); text-transform: uppercase; white-space: nowrap;
  }
  .holder__role { font-size: 11px; color: var(--muted); margin-top: 2px; }
  .holder__rule { width: 64px; height: 2px; background: var(--lime); margin-top: 8px; }

  .contacts { position: absolute; left: 38px; top: 122px; list-style: none; }
  .contacts li {
    display: flex; align-items: center; gap: 9px;
    font-size: 11px; color: var(--text); height: 22px; white-space: nowrap;
  }
  .contacts .icon {
    flex: none; width: 16px; height: 16px; border-radius: 3px; background: var(--lime);
    display: flex; align-items: center; justify-content: center;
  }
  .contacts svg { width: 10px; height: 10px; }

  .brand-band {
    position: absolute; left: 258px; top: 150px; right: 0; height: 82px;
    background: var(--forest); border-radius: 20px 0 0 20px;
    display: flex; align-items: center; padding-left: 30px; gap: 12px;
  }
  .brand-mark { flex: none; width: 14px; height: 14px; background: var(--lime); }
  .brand-name {
    font-weight: 500; font-size: 32px; color: var(--paper);
    letter-spacing: .5px; white-space: nowrap;
  }

  /* Back: logo side */
  .card--back { background: var(--forest); }
  .tab { position: absolute; width: 110px; height: 20px; background: var(--lime); }
  .tab--top { left: 68px; top: 0; border-radius: 0 0 8px 8px; }
  .tab--bottom { right: 68px; bottom: 0; border-radius: 8px 8px 0 0; }
  .back-brand {
    position: absolute; inset: 0;
    display: flex; align-items: center; justify-content: center; gap: 16px;
  }
  .back-brand .brand-mark { width: 20px; height: 20px; }
  .back-brand .brand-name { font-size: 46px; }
</style>
</head>
<body>
<main class="sheet">
  <section class="card card--front" aria-label="Card front with contact details">
    <div class="holder">
      <p class="holder__name">Mara Keller</p>
      <p class="holder__role">Manager</p>
      <div class="holder__rule"></div>
    </div>
    <ul class="contacts">
      <li><span class="icon"><svg viewBox="0 0 10 10"><path d="M2 1l2 0 .6 2-1 .8a5 5 0 0 0 2.6 2.6l.8-1 2 .6v2c0 .6-.4 1-1 1A8 8 0 0 1 1 2c0-.6.4-1 1-1z" fill="#fff"/></svg></span>+41 79555 0142</li>
      <li><span class="icon"><svg viewBox="0 0 10 10"><rect x="1" y="2" width="8" height="6" fill="none" stroke="#fff" stroke-width="1"/><path d="M1 2l4 3.5L9 2" fill="none" stroke="#fff" stroke-width="1"/></svg></span>mara@zub.capital</li>
      <li><span class="icon"><svg viewBox="0 0 10 10"><path d="M5 9.5S1.8 6 1.8 4a3.2 3.2 0 0 1 6.4 0C8.2 6 5 9.5 5 9.5z" fill="#fff"/><circle cx="5" cy="4" r="1.2" fill="#84bc3a"/></svg></span>Arvendal, Lorenmark</li>
      <li><span class="icon"><svg viewBox="0 0 10 10"><path d="M2 8L8 2M4 2h4v4" fill="none" stroke="#fff" stroke-width="1.4"/></svg></span>www.zub.capital</li>
    </ul>
    <div class="brand-band">
      <span class="brand-mark"></span>
      <span class="brand-name">Zub Capital</span>
    </div>
  </section>

  <section class="card card--back" aria-label="Card back with company name">
    <div class="tab tab--top"></div>
    <div class="back-brand">
      <span class="brand-mark"></span>
      <span class="brand-name">Zub Capital</span>
    </div>
    <div class="tab tab--bottom"></div>
  </section>
</main>
</body>
</html>
```